Probate (Legal) Wordpress Design with Coding for Online Company

I need a Wordpress design with coding, pictures, content to be provided by me, fully responsive, and development. This is for a 6-7 page design.

Pages Needed: Home/About/Probate/Process/FAQ/Contact Us/Blog.

The home page should be organized as followed:
-Steps in Probate: Gather; Implement; Close (each step will come with content)
-Flat-Fee Price & Savings: Content will go here with a button to contact us (phone number) or just the phone number.
-You Have Questions, We Have Answers: five questions with content. Only one question answer to show at a time when clicked on the question from the list.
-Get to Know Us: a brief description with content about what we do and who we are.

Main image slogan: Helping Californians deal with loss with DIGNITY & UNDERSTATING (you may use a better slogan if you wish).

The Contact page should not have a map since we are an online company. We service the entire state of California in every county and city.

The About page should be simple, direct, and easy on the eye. It should have a brief description of who we are and it should have no more than 6 reasons why the client should hire us.

About our online California company. We are not attorneys but legal document assistants who prepare legal documents for probate estate when someone dies with or without a will and assets need to be distributed. We have a flat-fee for Formal Probate of $999 and $699 for Informal Probate. We are an online company and offer our services to the entire state of California in every county. We do everything over the phone and email. The turn around time for us to prepare the initial legal paperwork for the client is within 3-5 business days. We can prepare, file, serve and manage a probate matter from petition to closing. We are not attorneys so our prices are very affordable compare to the attorney.

The company name for the website will be www.velmarhollow.com, The Velmar Hollow Group.

I do not have a logo yet. The colors of the website should be easy on the eye and calming. THE SITE SHOULD BE SIMPLE AND STRAIGHT TO THE POINT. EASY TO NAVIGATE.

The company phone number should be very visible and should stand out to the client. It should also be clickable and ready to dial for smartphone users.

I do not want a contact form on the homepage. THE MAIN THING IS FOR THE POTENTIAL CLIENT TO CALL OUR OFFICE TO SIGN UP.

I do like some images of family or people since we are dealing with people who just lost a loved one. Not all the images have to be of people.

The site should not look like we practice law or that people can mistake us for attorneys.

Target Market(s)

People who just lost a loved one who had property, assets, in California but died with or without a will or trust. This is for people looking to hire non-attorneys.

Coding

Coded - Design and coding required

Font styles to use
Serif

Colors

Designer to choose colors to be used in the design.

Requirements
Must have
• Refer to Project Description.
Nice to have
• The sample images provided is what I am attracted to for the homepage image.
Should not have

```html
<!DOCTYPE html>
<html lang="en">
<head>
<meta charset="utf-8">
<title>About Us – The Velmar Hollow Group</title>
<link href="https://fonts.googleapis.com/css2?family=Crimson+Text:wght@600;700&family=Open+Sans:wght@400;600&display=swap" rel="stylesheet">
<style>
  :root {
    --orange: #f7871e;
    --teal: #1a6e8e;
    --ink: #222;
    --body: #555;
    --blue-panel: #1b87ab;
    --amber-panel: #c27a1e;
    --white: #fff;
    --rule: #333;
  }
  * { box-sizing: border-box; margin: 0; padding: 0; }
  html, body { width: 890px; height: 1200px; overflow: hidden; background: var(--white); }
  body { position: relative; font-family: "Open Sans", sans-serif; color: var(--ink); }

  .top-rule { position: absolute; left: 0; top: 0; width: 890px; height: 2px; background: var(--orange); }
  .call-tab {
    position: absolute; left: 588px; top: 0; width: 228px; height: 33px;
    background: var(--orange); border-radius: 0 0 22px 22px;
    display: flex; align-items: center; justify-content: center; gap: 8px;
    color: var(--white); font-weight: 600; font-size: 12.5px;
  }
  .brand {
    position: absolute; left: 74px; top: 56px;
    font-family: "Crimson Text", serif; font-weight: 700; font-size: 15px;
    color: var(--teal); letter-spacing: .5px;
  }
  .main-nav {
    position: absolute; left: 339px; top: 57px; width: 478px;
    display: flex; justify-content: space-between;
    font-size: 11.5px; text-transform: uppercase; color: var(--ink);
  }

  .hero {
    position: absolute; left: 0; top: 93px; width: 890px; height: 143px;
    background: linear-gradient(90deg, #5f5d5a 0%, #6c6763 45%, #8a7462 70%, #7b6a5c 100%);
  }
  .hero-title {
    position: absolute; left: 74px; top: 138px;
    font-family: "Crimson Text", serif; font-weight: 600; font-size: 41px;
    color: var(--white); letter-spacing: 1px; line-height: 1;
  }

  .about-photo {
    position: absolute; left: 74px; top: 310px; width: 308px; height: 230px; border-radius: 3px;
    background: linear-gradient(120deg, #8f7a5f 0%, #b69066 40%, #d27a3a 75%, #6b4a2c 100%);
  }
  .about-text { position: absolute; left: 403px; top: 310px; width: 414px; }
  .section-title {
    font-family: "Crimson Text", serif; font-weight: 600; font-size: 25px;
    color: var(--teal); letter-spacing: .5px; line-height: 1.2;
  }
  .about-text .rule { width: 69px; height: 2px; background: var(--teal); margin: 12px 0 18px; }
  .about-text p { font-size: 10.4px; line-height: 16.5px; color: var(--body); text-align: justify; margin-bottom: 12px; }

  .panel { position: absolute; top: 613px; height: 361px; width: 445px; color: var(--white); }
  .panel.what { left: 0; background: linear-gradient(135deg, #1f94b8 0%, #1a86aa 50%, #1c7da0 100%); }
  .panel.who { left: 445px; background: linear-gradient(135deg, #b8761f 0%, #c7831f 55%, #b3701c 100%); }
  .panel-body { position: absolute; left: 74px; top: 47px; width: 350px; }
  .panel.who .panel-body { left: 24px; }
  .panel h2 { font-family: "Crimson Text", serif; font-weight: 600; font-size: 23px; letter-spacing: .5px; line-height: 1.2; }
  .panel .rule { width: 80px; height: 1.5px; background: var(--white); margin: 10px 0 27px; }
  .panel p { font-size: 10.6px; font-weight: 600; line-height: 17.6px; margin-bottom: 17px; }
  .btn-outline {
    display: inline-block; margin-top: 10px; width: 84px; height: 40px;
    border: 1.5px solid var(--white); text-align: center; line-height: 37px;
    font-size: 12px; font-weight: 600;
  }

  .footer-nav {
    position: absolute; left: 0; top: 1025px; width: 890px;
    display: flex; justify-content: center; gap: 20px;
    font-size: 11.5px; text-transform: uppercase; color: var(--ink);
  }
  .footer-contact {
    position: absolute; left: 0; top: 1081px; width: 890px;
    display: flex; justify-content: center; gap: 32px; font-size: 16px; color: var(--ink);
  }
  .contact-item { display: flex; align-items: center; gap: 10px; }
  .icon-ring { width: 34px; height: 34px; border: 1.5px solid var(--ink); border-radius: 50%; display: flex; align-items: center; justify-content: center; }
  .footer-rule { position: absolute; left: 74px; top: 1140px; width: 743px; height: 1px; background: var(--rule); }
  .copyright { position: absolute; left: 0; top: 1160px; width: 890px; text-align: center; font-size: 11.5px; color: var(--ink); }
</style>
</head>
<body>
  <div class="top-rule"></div>
  <div class="call-tab">
    <svg width="12" height="12" viewBox="0 0 12 12"><rect width="12" height="12" rx="2" fill="#fff"/><path d="M3.3 2.6l1.4-.2.7 1.8-.9.7c.4.9 1.1 1.6 2 2l.7-.9 1.8.7-.2 1.4c-3 .3-5.8-2.5-5.5-5.5z" fill="#f7871e"/></svg>
    <span>Call Us At: +180 555 0147</span>
  </div>

  <div class="brand">THE VELMAR HOLLOW GROUP</div>

  <nav class="main-nav">
    <span>Home</span><span>About</span><span>Probate</span><span>Process</span><span>FAQ</span><span>Contact Us</span><span>Blog</span>
  </nav>

  <div class="hero" role="img" aria-label="Banner photo of a mother embracing her children"></div>
  <h1 class="hero-title">ABOUT US</h1>

  <div class="about-photo" role="img" aria-label="Photo of a mother holding her young son"></div>
  <section class="about-text">
    <h2 class="section-title">ABOUT VELMAR HOLLOW</h2>
    <div class="rule"></div>
    <p>About our online California company. We are not attorneys but legal document assistants who prepare legal documents for probate estate when someone dies with or without a will and assets need to be distributed. We have a flat-fee for Formal Probate of $999 and $699 for Informal Probate. We are an online company and offer our services to the entire state of California in every county.</p>
    <p>We do everything over the phone and email. The turn around time for us to prepare the initial legal paperwork for the client is within 3-5 business days. We can prepare, file, serve and manage a probate matter from petition to closing. We are not attorneys so our prices are very affordable compare to the attorney.</p>
  </section>

  <section class="panel what" role="img" aria-label="Blue-tinted photo of hands over paperwork">
    <div class="panel-body">
      <h2>WHAT WE DO</h2>
      <div class="rule"></div>
      <p>Sed ut perspiciatis unde omnis iste natus error sit voluptatem accusantium doloremque laudantium, totam rem aperiam, eaque ipsa quae ab illo inventore veritatis et quasi architecto beatae.</p>
      <p>Nemo enim ipsam voluptatem quia voluptas sit aspernatur aut odit aut fugit, sed quia consequuntur magni dolores eos qui ratione voluptatem.</p>
      <span class="btn-outline">READ MORE</span>
    </div>
  </section>
  <section class="panel who" role="img" aria-label="Amber-tinted photo of a hand signing a document with a pen">
    <div class="panel-body">
      <h2>WHO WE ARE</h2>
      <div class="rule"></div>
      <p>Sed ut perspiciatis unde omnis iste natus error sit voluptatem accusantium doloremque laudantium, totam rem aperiam, eaque ipsa quae ab illo inventore veritatis et quasi architecto beatae.</p>
      <p>Nemo enim ipsam voluptatem quia voluptas sit aspernatur aut odit aut fugit, sed quia consequuntur magni dolores eos qui ratione voluptatem.</p>
      <span class="btn-outline">READ MORE</span>
    </div>
  </section>

  <nav class="footer-nav">
    <span>Home</span><span>|</span><span>About</span><span>|</span><span>Probate</span><span>|</span><span>Process</span><span>|</span><span>FAQ</span><span>|</span><span>Contact Us</span><span>|</span><span>Blog</span>
  </nav>

  <div class="footer-contact">
    <div class="contact-item">
      <span class="icon-ring"><svg width="16" height="16" viewBox="0 0 16 16"><path d="M3.2 1.5l2.4-.3 1.1 3-1.4 1.1c.7 1.6 1.9 2.8 3.4 3.4l1.1-1.4 3 1.1-.3 2.4c-5 .6-9.9-4.3-9.3-9.3z" fill="#222"/></svg></span>
      <span>+180 555 0147</span>
    </div>
    <div class="contact-item">
      <span class="icon-ring"><svg width="16" height="16" viewBox="0 0 16 16"><rect x="1.5" y="3.5" width="13" height="9" rx="1.5" fill="none" stroke="#222" stroke-width="1.4"/><path d="M2 4.5l6 4.5 6-4.5" fill="none" stroke="#222" stroke-width="1.4"/></svg></span>
      <span>info@velmarhollow.com</span>
    </div>
  </div>

  <div class="footer-rule"></div>
  <p class="copyright">Copyrights @ 2017 The Velmar Hollow Group. All Rights Reserved.</p>
</body>
</html>
```